product development company BRVEMKO LLC business card

We need a business card design for a company based in Texas called 'BRVEMKO LLC'. Our first product is a illuminated portable ice chest that is called ' Copper Harbor coolers'. Copper harbor coolers is trademarked. I would like to have the copper harbor trademark somewhere on the card as well as the BRVEMKO LLC name.

Target Market(s)

outdoor industry

Industry/Entity Type

Business

Contact Information for Business Card

i would like to have BRVEMKO LLC logo larger than the Copper harbor coolers logo.

Font styles to use
Serif
Sans Serif

```html
<!DOCTYPE html>
<html lang="en">
<head>
<meta charset="utf-8">
<title>BRVEMKO LLC business card</title>
<link rel="stylesheet" href="https://fonts.googleapis.com/css2?family=Open+Sans:wght@400;700&display=swap">
<style>
  :root {
    --backdrop: #6b4630;
    --card: #050505;
    --ink: #ffffff;
    --ink-soft: #e9e9e9;
  }
  * { margin: 0; padding: 0; box-sizing: border-box; }
  html, body { width: 1200px; height: 1000px; overflow: hidden; }
  body {
    position: relative;
    background: var(--backdrop);
    font-family: "Open Sans", Arial, sans-serif;
    color: var(--ink);
  }
  .card {
    position: absolute;
    left: 265px;
    width: 666px;
    height: 397px;
    background: var(--card);
  }
  .card--front { top: 73px; }
  .card--second { top: 532px; }
  .company {
    position: absolute;
    left: 33px;
    top: 42px;
    font-size: 38px;
    font-weight: 400;
    letter-spacing: 2px;
    line-height: 1;
    color: var(--ink);
  }
  .person { position: absolute; left: 33px; top: 181px; }
  .person__name { font-size: 20px; font-weight: 700; line-height: 1.2; }
  .person__role { font-size: 15.5px; color: var(--ink-soft); line-height: 1.3; }
  .contacts {
    position: absolute;
    left: 33px;
    top: 244px;
    list-style: none;
    font-size: 15.5px;
    color: var(--ink-soft);
  }
  .contacts li { display: flex; align-items: center; height: 23px; }
  .contacts li.contacts__address { margin-top: 5px; }
  .contacts svg { width: 16px; height: 16px; margin-right: 6px; fill: var(--ink); flex: none; }
  .product-mark {
    position: absolute;
    left: 454px;
    top: 286px;
    display: flex;
    align-items: center;
    gap: 8px;
    font-size: 19px;
    font-weight: 700;
    line-height: 1.05;
    color: var(--ink);
  }
  .product-mark__square { width: 34px; height: 34px; background: var(--ink); flex: none; }
</style>
</head>
<body>

<section class="card card--front">
  <h1 class="company">BRVEMKO LLC</h1>
  <div class="person">
    <p class="person__name">MARCUS ALVARADO</p>
    <p class="person__role">Managing Director</p>
  </div>
  <ul class="contacts">
    <li><svg viewBox="0 0 16 16" aria-hidden="true"><path d="M5 1h6a1 1 0 0 1 1 1v12a1 1 0 0 1-1 1H5a1 1 0 0 1-1-1V2a1 1 0 0 1 1-1zm1 2v6h4V3zm2 9a1 1 0 1 0 0 2 1 1 0 0 0 0-2z"/></svg>+ 000 000 0000</li>
    <li><svg viewBox="0 0 16 16" aria-hidden="true"><path d="M1 6c0-2 3-3 7-3s7 1 7 3v1h-3V5.5H4V7H1zm3 2h8l2 5H2z"/></svg>+ 000 000 0000</li>
    <li><svg viewBox="0 0 16 16" aria-hidden="true"><path d="M1 4h14v9H1zm1 1 6 4 6-4"/><path d="M2 5l6 4 6-4" fill="none" stroke="#050505"/></svg>info@brvemkocopperharbor.com</li>
    <li><svg viewBox="0 0 16 16" aria-hidden="true"><path d="M8 1a7 7 0 1 0 0 14A7 7 0 0 0 8 1zm0 1.5c1 1 1.6 2.8 1.7 4.7H6.3C6.4 5.3 7 3.5 8 2.5zM6.3 8.8h3.4c-.1 1.9-.7 3.7-1.7 4.7-1-1-1.6-2.8-1.7-4.7z"/></svg>www.brvemkocopperharbor.com</li>
    <li class="contacts__address"><svg viewBox="0 0 16 16" aria-hidden="true"><path d="M8 0a5.5 5.5 0 0 0-5.5 5.5C2.5 10 8 16 8 16s5.5-6 5.5-10.5A5.5 5.5 0 0 0 8 0zm0 3.5a2 2 0 1 1 0 4 2 2 0 0 1 0-4z"/></svg>4180 W. Mesa Blvd. Alton, TX 78573</li>
  </ul>
  <div class="product-mark"><span class="product-mark__square"></span><span>Copper<br>Harbor</span></div>
</section>

<section class="card card--second">
  <p class="company">BRVEMKO LLC</p>
  <div class="person">
    <p class="person__name">MARCUS ALVARADO</p>
    <p class="person__role">Managing Director</p>
  </div>
  <ul class="contacts">
    <li><svg viewBox="0 0 16 16" aria-hidden="true"><path d="M5 1h6a1 1 0 0 1 1 1v12a1 1 0 0 1-1 1H5a1 1 0 0 1-1-1V2a1 1 0 0 1 1-1zm1 2v6h4V3zm2 9a1 1 0 1 0 0 2 1 1 0 0 0 0-2z"/></svg>+ 000 000 0000</li>
    <li><svg viewBox="0 0 16 16" aria-hidden="true"><path d="M1 6c0-2 3-3 7-3s7 1 7 3v1h-3V5.5H4V7H1zm3 2h8l2 5H2z"/></svg>+ 000 000 0000</li>
    <li><svg viewBox="0 0 16 16" aria-hidden="true"><path d="M1 4h14v9H1z"/><path d="M2 5l6 4 6-4" fill="none" stroke="#050505"/></svg>info@brvemkocopperharbor.com</li>
    <li><svg viewBox="0 0 16 16" aria-hidden="true"><path d="M8 1a7 7 0 1 0 0 14A7 7 0 0 0 8 1zm0 1.5c1 1 1.6 2.8 1.7 4.7H6.3C6.4 5.3 7 3.5 8 2.5zM6.3 8.8h3.4c-.1 1.9-.7 3.7-1.7 4.7-1-1-1.6-2.8-1.7-4.7z"/></svg>www.brvemkocopperharbor.com</li>
    <li class="contacts__address"><svg viewBox="0 0 16 16" aria-hidden="true"><path d="M8 0a5.5 5.5 0 0 0-5.5 5.5C2.5 10 8 16 8 16s5.5-6 5.5-10.5A5.5 5.5 0 0 0 8 0zm0 3.5a2 2 0 1 1 0 4 2 2 0 0 1 0-4z"/></svg>4180 W. Mesa Blvd. Alton, TX 78573</li>
  </ul>
  <div class="product-mark"><span class="product-mark__square"></span><span>Copper<br>Harbor</span></div>
</section>

</body>
</html>
```